Flat bootstrap design for existing site

I'm looking for a modern flat design based around an existing logo. This has to be a custom design (no external templates), and implemented into a bootstrap framework.

The logo is attached as 2 versions - choose whichever you want, that flows better with whatever design you choose.

Added screenshots of the existing site (currently using the default bootstrap layouts). Please make your designs around those pages in the screenshots (i.e. the homepage only has the postal code input and the header). The active page has 3 screenshots, because I wanted to illustrate the other states that would be visible (in the table rows).

This is a moving/junk removal website, just for some context.

Here's some example websites (flat designs) that I like, just to give you an idea of what I'm after.

https://www.plimvora.com/
https://dacklow.com/
https://trevanu.com/
https://quobrintal.com/en/

Coding

Coded - Design and coding required

Number of Pages Required

5+ page

Colors

Designer to choose colors to be used in the design.

Requirements
Must have
• It must be a modern/simple flat design, that is built around the existing logo (attached).
• It has to be implemented using bootstrap.

```html
<!DOCTYPE html>
<html lang="en">
<head>
<meta charset="utf-8">
<title>Haulmo — Junk Removal</title>
<link href="https://fonts.googleapis.com/css2?family=Montserrat:wght@400;500;600;800&display=swap" rel="stylesheet">
<style>
  :root {
    --brand-blue: #4ec6f2;
    --hero-top: #5ccbf3;
    --hero-bottom: #43b6e2;
    --accent-orange: #ff9a33;
    --ink: #111111;
    --muted: #6b6b6b;
    --white: #ffffff;
    --line: #e6e6e6;
  }
  * { box-sizing: border-box; margin: 0; padding: 0; }
  html, body { width: 1200px; height: 705px; overflow: hidden; background: var(--white); }
  body { font-family: "Montserrat", sans-serif; position: relative; }

  .site-header { position: absolute; top: 0; left: 0; width: 1200px; height: 85px; background: var(--white); }
  .brand { position: absolute; left: 90px; top: 24px; display: flex; align-items: center; gap: 8px;
    color: var(--brand-blue); font-weight: 800; font-size: 32px; letter-spacing: 1px; text-decoration: none; }
  .brand-dot { width: 22px; height: 22px; border-radius: 50%; background: var(--brand-blue); }
  .main-nav a { position: absolute; top: 35px; font-size: 14px; font-weight: 600; color: var(--ink); text-decoration: none; }
  .nav-book { left: 475px; }
  .nav-how { left: 558px; }
  .btn-driver, .btn-signin { position: absolute; top: 21px; height: 43px; border-radius: 22px;
    display: flex; align-items: center; justify-content: center; font-size: 14px; font-weight: 600; text-decoration: none; }
  .btn-driver { left: 718px; width: 178px; background: var(--brand-blue); color: var(--white); }
  .btn-signin { left: 917px; width: 133px; background: var(--white); color: var(--ink); border: 1px solid var(--line); }

  .hero { position: absolute; top: 85px; left: 0; width: 1200px; height: 554px; }
  .hero-photo { position: absolute; inset: 0; background: linear-gradient(160deg, var(--hero-top), var(--hero-bottom)); }
  .hero-title { position: absolute; top: 210px; left: 0; width: 1136px; text-align: center;
    color: var(--white); font-weight: 800; font-size: 36px; }
  .booking-form { position: absolute; top: 272px; left: 252px; width: 676px; height: 63px;
    border: 1px solid rgba(255,255,255,0.8); }
  .postal-input { position: absolute; left: 17px; top: 0; height: 63px; line-height: 63px;
    color: var(--white); font-size: 18px; font-weight: 400; }
  .btn-book { position: absolute; left: 522px; top: 9px; width: 142px; height: 42px; border-radius: 21px;
    background: var(--accent-orange); color: var(--white); font-size: 14px; font-weight: 600;
    display: flex; align-items: center; justify-content: center; }

  .site-footer { position: absolute; top: 639px; left: 0; width: 1200px; height: 66px;
    text-align: center; line-height: 66px; color: var(--muted); font-size: 14px; }
</style>
</head>
<body>
  <header class="site-header">
    <a class="brand" href="#"><span class="brand-dot"></span>HAULMO</a>
    <nav class="main-nav">
      <a class="nav-book" href="#">BOOK</a>
      <a class="nav-how" href="#">HOW IT WORKS</a>
    </nav>
    <a class="btn-driver" href="#">BECOME A DRIVER</a>
    <a class="btn-signin" href="#">SIGN IN</a>
  </header>

  <section class="hero">
    <div class="hero-photo" role="img" aria-label="Person carrying a cardboard moving box in front of a house, tinted blue"></div>
    <h1 class="hero-title">Need junk removed ? Book Now</h1>
    <div class="booking-form">
      <span class="postal-input">Postal Code</span>
      <span class="btn-book">BOOK NOW</span>
    </div>
  </section>

  <footer class="site-footer">© 2017 Company Name &nbsp;| All Rights Reserved</footer>
</body>
</html>
```